Private Investment Firm Needs PowerPoint Presentation Template

Design PowerPoint template, take Pinebrook-submitted rough presentation draft, and drop it into new template. See attached Project Brief file for more detail.
Updates

Some decent designs have been submitted but they seem to lack the understanding of our target markets. I am hopeful that more time and feedback will result in better results.

Target Market(s)

Private company owners and intermediaries.

Font styles to use
Serif

Colors
3176b5

Requirements
Must have
• See attached Project Brief.
Nice to have
Should not have
• No B2C fluff--this is a B2B project.

```html
<!DOCTYPE html>
<html lang="en">
<head>
<meta charset="utf-8">
<title>Pinebrook Capital – Non-Control Capital Deck</title>
<link rel="stylesheet" href="https://fonts.googleapis.com/css2?family=Cinzel:wght@400;600&family=Montserrat:wght@400;500;600;700&display=swap">
<style>
:root{
  --blue:#1f6fb8;
  --blue-deep:#0f55a0;
  --blue-mid:#2f86cc;
  --blue-light:#4a9ad6;
  --sky:#5cc3ea;
  --navy:#0d1e38;
  --navy-box:#0f4a86;
  --charcoal:#4b4e52;
  --ink:#2f3236;
  --muted:#5d6166;
  --paper:#ffffff;
  --paper-shade:#e6e9ed;
  --canvas-a:#b8b9bb;
  --canvas-b:#9a9b9d;
}
*{margin:0;padding:0;box-sizing:border-box}
html,body{width:1043px;height:1200px;overflow:hidden}
body{
  position:relative;
  background:radial-gradient(ellipse at 50% 40%,var(--canvas-a),var(--canvas-b));
  font-family:"Montserrat",sans-serif;color:var(--ink);
}
.slide{
  position:absolute;width:441px;height:249px;overflow:hidden;
  background:linear-gradient(160deg,var(--paper) 30%,var(--paper-shade));
  box-shadow:0 3px 8px rgba(0,0,0,.35);
}
.slide>*{position:absolute}
.slide-frame{left:0;top:0;width:441px;height:249px}
.col-left{left:51px}.col-right{left:545px}
.row-1{top:51px}.row-2{top:340px}.row-3{top:616px}.row-4{top:900px}

.brand{display:flex;align-items:center;gap:4px;font-size:7px;font-weight:600;letter-spacing:.8px;color:var(--navy)}
.brand-dot{width:12px;height:12px;border-radius:50%;background:var(--blue)}
.footer-brand{left:45px;top:221px}
.footer-url{left:230px;top:224px;font-size:6.5px;color:var(--ink)}
.footer-url b{color:var(--blue);font-weight:600}
.page-no{left:404px;top:224px;font-size:5.5px;color:#fff;font-weight:700}

/* title slide */
.cover-title{left:71px;top:44px;width:300px;text-align:center;font-family:"Cinzel",serif;font-size:21px;line-height:24px;color:var(--blue)}
.cover-sub{left:71px;top:108px;width:300px;text-align:center;font-size:6px;line-height:9px;color:var(--muted)}
.cover-sub b{color:var(--blue);font-weight:600}
.cover-date{left:171px;top:150px;width:100px;height:26px;border:1px solid var(--ink);font-size:14px;text-align:center;line-height:24px;color:var(--ink)}
.cover-brand{left:176px;top:194px;font-size:9px}
.cover-brand .brand-dot{width:16px;height:16px}
.cover-url{left:71px;top:228px;width:300px;text-align:center;font-size:9.5px;color:var(--ink)}
.cover-url b{color:var(--blue);font-weight:600}

/* intro */
.slide-heading{left:0;width:410px;text-align:center;font-weight:700;color:var(--blue)}
.intro-heading{top:30px;font-size:13px;letter-spacing:.6px}
.intro-list{left:57px;top:62px;width:320px;list-style:none;font-size:6.3px;line-height:7.6px;color:var(--muted)}
.intro-list>li{position:relative;padding-left:12px;margin-bottom:8px}
.intro-list>li::before{content:"•";position:absolute;left:0;color:var(--blue)}
.intro-list ul{list-style:none;margin-top:2px}
.intro-list ul li{padding-left:18px;position:relative}
.intro-list ul li::before{content:"✓";position:absolute;left:10px;color:var(--blue);font-size:5px}

/* questionnaire */
.q-kicker{top:14px;left:0;width:441px;text-align:center;font-size:8px;font-weight:600;color:var(--ink)}
.q-banner{left:52px;top:31px;width:352px;height:36px}
.q-banner-text{left:52px;top:36px;width:352px;text-align:center;font-family:"Cinzel",serif;font-size:9.5px;line-height:12px;color:#fff}
.q-tab{left:176px;top:72px;width:87px;height:12px;background:var(--navy);color:#fff;font-size:7px;font-weight:600;text-align:center;line-height:12px}
.q-col{top:89px;width:175px;font-size:3.9px;line-height:4.6px;color:var(--muted);list-style:none}
.q-col li{position:relative;padding-left:13px;margin-bottom:4px}
.q-col .num{position:absolute;left:0;top:0;width:8px;height:8px;border-radius:50%;background:var(--blue);color:#fff;font-size:4.5px;font-weight:700;text-align:center;line-height:8px}
.q-col strong{display:block;color:var(--navy);font-weight:700}
.q-col em{font-style:normal;color:var(--blue);font-weight:700}
.q-left{left:20px}.q-right{left:199px}

/* capital stack */
.stack-banner{left:59px;top:19px;width:310px;height:26px}
.stack-banner-text{left:59px;top:25px;width:310px;text-align:center;font-family:"Cinzel",serif;font-size:11px;color:#fff}
.stack-bar{left:50px;top:51px;width:321px;height:16px;background:var(--sky);color:var(--navy);font-size:6.5px;font-weight:700;text-align:center;line-height:16px}
.stack-list{left:50px;width:98px;list-style:none;font-size:3.8px;text-align:center;color:var(--ink)}
.stack-list li{height:11px;line-height:11px;margin-bottom:1px;background:linear-gradient(#f2f3f5,#d6d9dd)}
.stack-list li.head{background:var(--blue);color:#fff;font-size:6px;font-weight:700}
.stack-senior{top:71px}.stack-junior{top:158px}
.stack-box{left:152px;width:219px;color:#dfe8f3;font-size:4.5px;line-height:5.6px;text-align:center;padding:0 10px;display:flex;flex-direction:column;justify-content:center}
.stack-box b{color:#fff;font-size:5px}
.stack-box-senior{top:71px;height:71px;background:var(--navy-box)}
.stack-box-junior{top:158px;height:50px;background:var(--navy)}
.stack-divider{left:50px;top:148px;width:321px;height:4px}

/* epilogue */
.epilogue-word{left:0;top:102px;width:441px;text-align:center;padding-left:0;font-size:27px;letter-spacing:1.5px;color:var(--charcoal);font-weight:500}
.epilogue-rule{left:206px;top:140px;width:30px;height:3px;background:var(--blue)}

/* quote */
.quote-open{left:94px;top:28px;font-family:"Cinzel",serif;font-size:48px;line-height:48px;color:#b8bcc1}
.quote-text{left:94px;top:70px;width:224px;font-size:10.5px;line-height:11.4px;color:var(--ink)}
.quote-cite{left:150px;top:172px;width:125px;text-align:right;font-size:6px;font-weight:700;color:var(--blue)}
.quote-close{left:280px;top:166px;font-family:"Cinzel",serif;font-size:48px;line-height:48px;color:#b8bcc1}

/* 12 uses */
.uses-title{top:27px;font-size:13.5px;left:0;width:441px;text-align:center;padding-right:30px}
.uses-grid{left:54px;top:57px;width:334px;height:149px;display:grid;grid-template-columns:repeat(4,1fr);grid-template-rows:repeat(3,1fr);gap:1px;background:#fff}
.use{padding:3px 4px;text-align:center;color:#fff;font-size:3.3px;line-height:4px}
.use h3{font-size:5.3px;line-height:6px;font-weight:700;margin-bottom:2px}
.use-r1{background:var(--blue-deep)}
.use-r2{background:var(--blue-mid)}
.use-r3{background:var(--blue-light)}

/* contact */
.contact-banner{left:155px;top:16px;width:126px;height:19px}
.contact-banner-text{left:155px;top:18px;width:126px;text-align:center;font-size:12px;letter-spacing:.6px;color:#fff;font-weight:500}
.contact-rail{left:52px;top:56px;width:1px;height:105px;background:#9aa0a6}
.contact-list{left:48px;top:52px;width:200px;list-style:none;font-size:6.6px;line-height:7.6px;color:var(--muted)}
.contact-list li{position:relative;padding-left:18px;margin-bottom:7px}
.contact-list li::before{content:"";position:absolute;left:1px;top:1px;width:5px;height:5px;border-radius:50%;background:#fff;border:1.5px solid #6c7278}
.contact-list strong{display:block;color:var(--blue);font-weight:600}
.contact-list .phone{color:var(--blue)}
.contact-list b{color:var(--blue);font-weight:600}
.contact-photo{left:316px;top:94px;width:98px;height:98px;border-radius:50%;border:3px solid #fff;background:radial-gradient(circle at 50% 45%,#8aa6c2,#2b5c8f 70%,#173c66)}
</style>
</head>
<body>

<!-- 1. Cover -->
<section class="slide col-left row-1">
  <svg class="slide-frame" viewBox="0 0 441 249" preserveAspectRatio="none">
    <defs><linearGradient id="bl1" x1="0" y1="0" x2="0" y2="1"><stop offset="0" stop-color="#1f6fb8"/><stop offset="1" stop-color="#2f8fd4"/></linearGradient></defs>
    <polygon points="0,0 40,0 0,120" fill="#4b4e52"/>
    <polygon points="412,0 441,0 441,249 350,249" fill="url(#bl1)"/>
  </svg>
  <h1 class="cover-title">Introduction to<br>Non-Control Capital</h1>
  <p class="cover-sub">The Lower Middle Market Private Company Strategy for<br>Raising Capital While <b>Maintaining Business Control</b></p>
  <div class="cover-date">Fall-2018</div>
  <div class="brand cover-brand"><span class="brand-dot"></span>PINEBROOK</div>
  <p class="cover-url">www.<b>pinebrookcapital</b>.com</p>
</section>

<!-- 2. Introduction -->
<section class="slide col-right row-1">
  <svg class="slide-frame" viewBox="0 0 441 249" preserveAspectRatio="none">
    <polygon points="0,0 30,0 0,90" fill="#4b4e52"/>
    <polygon points="412,0 441,0 441,249 350,249" fill="url(#bl1)"/>
  </svg>
  <h2 class="slide-heading intro-heading">INTRODUCTION</h2>
  <ul class="intro-list">
    <li>Private company owners have traditionally considered two capital raising options
      <ul><li>Borrow from a local bank, or</li><li>Sell most or all of the company to a change-of-control investor (aka Buyout firm)</li></ul></li>
    <li>An alternative most have not considered is the raising of Non-Control Capital, capital that is invested into the business yet allows those same owners to retain controlling interest in their company</li>
    <li>Non-Control Capital is not appropriate for every private company owner but neither is a Change-of-Control sale</li>
    <li>The key is to determine what the business and owners require, and then partner with an investor best aligned with those needs so that long-term company growth, and personal goals, can both be achieved</li>
  </ul>
  <div class="brand footer-brand"><span class="brand-dot"></span>PINEBROOK</div>
  <p class="footer-url">www.<b>pinebrookcapital</b>.com</p>
  <span class="page-no">1.</span>
</section>

<!-- 3. Questionnaire -->
<section class="slide col-left row-2">
  <svg class="slide-frame" viewBox="0 0 441 249" preserveAspectRatio="none">
    <polygon points="0,0 38,0 0,110" fill="#4b4e52"/>
    <polygon points="412,0 441,0 441,249 350,249" fill="url(#bl1)"/>
  </svg>
  <p class="q-kicker">Non-Control Capital Questionnaire</p>
  <svg class="q-banner" viewBox="0 0 352 36" preserveAspectRatio="none">
    <polygon points="8,0 14,0 6,36 0,36" fill="#4b4e52"/>
    <polygon points="20,0 344,0 336,36 12,36" fill="#1f6fb8"/>
    <polygon points="346,0 352,0 344,36 338,36" fill="#4b4e52"/>
  </svg>
  <p class="q-banner-text">The Critical Questions to Ask of<br>Any Prospective Non-Control Investor</p>
  <div class="q-tab">Questions</div>
  <ol class="q-col q-left">
    <li><span class="num">1</span><strong>How many years has the firm been investing Non-Control Capital?</strong><em>Best Answer:</em> 5+ years investing as a team within the current firm. Indicates comfort and experience evaluating and making NCC investments with each other and increases likelihood of close.</li>
    <li><span class="num">2</span><strong>How many fully-invested Non-Control Capital funds in the firm's history?</strong><em>Best Answer:</em> 2+ fully-invested funds. Indicates experience and ability to close deals with the current regime—those without it may only be testing the waters.</li>
    <li><span class="num">3</span><strong>What percentage of the firm's voting investment committee are full-time Non-Control Capital investors?</strong><em>Best Answer:</em> Super-majority. Indicates commitment, experience, and focus on NCC and overcomes dependency on buyout heritage, if any.</li>
    <li><span class="num">4</span><strong>What is the number of Non-Control Capital investments made with the current firm and team?</strong><em>Best Answer:</em> 20+. Indicates long-term experience and comfort with current team, investment committee, and NCC investment assessment.</li>
  </ol>
  <ol class="q-col q-right">
    <li><span class="num">5</span><strong>What percentage of portfolio investments made are "sponsorless" (those without a change-of-control investor)?</strong><em>Best Answer:</em> 80%+ of all investments closed in the last 5 years (assumes current transaction is also sponsorless). Indicates ability to add-value as a sole minority investor and not simply as a back-up to another sponsor.</li>
    <li><span class="num">6</span><strong>Can the investor show quantifiable proof of their ability to assist portfolio companies with growth and improvement (assumes more than 20 exited Non-Control investments)?</strong><em>Best Answer:</em> Yes (company owners should evaluate investors on actual historical revenue, EBITDA, and employee growth impact and the results should exceed what current management has achieved on their own over the past 5 years). Indicates true value-added ability to help owners grow their businesses. Those without proof of their impact, or who are unwilling to disclose it, should be excluded.</li>
  </ol>
  <div class="brand footer-brand"><span class="brand-dot"></span>PINEBROOK</div>
  <p class="footer-url">www.<b>pinebrookcapital</b>.com</p>
  <span class="page-no">2.</span>
</section>

<!-- 4. Capital stack -->
<section class="slide col-right row-2">
  <svg class="slide-frame" viewBox="0 0 441 249" preserveAspectRatio="none">
    <polygon points="0,0 30,0 0,90" fill="#4b4e52"/>
    <polygon points="412,0 441,0 441,249 350,249" fill="url(#bl1)"/>
  </svg>
  <svg class="stack-banner" viewBox="0 0 310 26" preserveAspectRatio="none">
    <polygon points="6,0 12,0 6,26 0,26" fill="#4b4e52"/>
    <polygon points="18,0 300,0 294,26 12,26" fill="#1f6fb8"/>
    <polygon points="304,0 310,0 304,26 298,26" fill="#4b4e52"/>
  </svg>
  <p class="stack-banner-text">Pinebrook Provides Junior Capital</p>
  <div class="stack-bar">Capital Stack Hierarchy.</div>
  <ul class="stack-list stack-senior">
    <li class="head">Senior Debt</li><li>Revolver</li><li>Asset-Based Loan</li><li>Senior Term Loan</li><li class="head">Combination</li><li>Unitranche</li>
  </ul>
  <div class="stack-box stack-box-senior"><b>Senior Debt Capital Providers</b>Paid back first, plays more of a lender than partner role, less value-added, less equity dilutive, less expensive capital, but not strategically focused</div>
  <svg class="stack-divider" viewBox="0 0 321 4" preserveAspectRatio="none">
    <rect width="321" height="4" fill="#0f4a86"/>
    <rect x="30" width="30" height="4" fill="#5cc3ea"/><rect x="100" width="30" height="4" fill="#5cc3ea"/><rect x="170" width="30" height="4" fill="#5cc3ea"/><rect x="240" width="30" height="4" fill="#5cc3ea"/>
  </svg>
  <ul class="stack-list stack-junior">
    <li class="head">Junior Capital</li><li>Subordinated Debt</li><li>Preferred Stock</li><li>Common Stock</li>
  </ul>
  <div class="stack-box stack-box-junior"><b>What Pinebrook Invests</b>Sits junior to all other capital (taking on more risk), plays a partner role, more value-added services provided, more expensive than senior debt, but supplies an engine for continuous improvement and growth</div>
  <div class="brand footer-brand"><span class="brand-dot"></span>PINEBROOK</div>
  <p class="footer-url">www.<b>pinebrookcapital</b>.com</p>
  <span class="page-no">3.</span>
</section>

<!-- 5. Epilogue -->
<section class="slide col-left row-3">
  <svg class="slide-frame" viewBox="0 0 441 249" preserveAspectRatio="none">
    <polygon points="0,0 40,0 0,120" fill="#4b4e52"/>
    <polygon points="412,0 441,0 441,249 350,249" fill="url(#bl1)"/>
  </svg>
  <h2 class="epilogue-word">EPILOGUE</h2>
  <div class="epilogue-rule"></div>
  <div class="brand footer-brand"><span class="brand-dot"></span>PINEBROOK</div>
  <p class="footer-url">www.<b>pinebrookcapital</b>.com</p>
  <span class="page-no">4.</span>
</section>

<!-- 6. Quote -->
<section class="slide col-right row-3">
  <svg class="slide-frame" viewBox="0 0 441 249" preserveAspectRatio="none">
    <polygon points="0,0 38,0 0,110" fill="#4b4e52"/>
    <polygon points="412,0 441,0 441,249 350,249" fill="url(#bl1)"/>
  </svg>
  <span class="quote-open">“</span>
  <blockquote class="quote-text">Our company had several business opportunities but I needed outside capital to take advantage of them. Why would I cede control of my business when we were at the exact point when raising outside capital would allow me to accelerate growth and achieve my life-long business and personal goals?!</blockquote>
  <p class="quote-cite">--Mark Ellison, CEO; The Harlan Group</p>
  <span class="quote-close">”</span>
  <div class="brand footer-brand"><span class="brand-dot"></span>PINEBROOK</div>
  <p class="footer-url">www.<b>pinebrookcapital</b>.com</p>
  <span class="page-no">6.</span>
</section>

<!-- 7. 12 uses -->
<section class="slide col-left row-4">
  <svg class="slide-frame" viewBox="0 0 441 249" preserveAspectRatio="none">
    <polygon points="0,0 38,0 0,110" fill="#4b4e52"/>
    <polygon points="412,0 441,0 441,249 350,249" fill="url(#bl1)"/>
  </svg>
  <h2 class="slide-heading uses-title">The 12 Primary Uses of Non-Control Capital</h2>
  <div class="uses-grid">
    <div class="use use-r1"><h3>Growth</h3>Capital used to organically expand a business, introduce new products, build a new facility, hire management or employees, enter new markets.</div>
    <div class="use use-r1"><h3>Acquisitions</h3>Capital used to acquire one or more competitors or to allow for further vertical or horizontal integration.</div>
    <div class="use use-r1"><h3>Partner or Shareholder Buy-Out</h3>Capital used to buy out an inactive or retiring partner or shareholder.</div>
    <div class="use use-r1"><h3>Management Buy-Out (MBO)</h3>When the incumbent management team buys most or all of the ownership of an inactive founder.</div>
    <div class="use use-r2"><h3>Management Buy-In (MBI)</h3>When an external, experienced executive buys a business from one or more inactive owners.</div>
    <div class="use use-r2"><h3>Family Ownership &amp; Wealth Transfer</h3>When junior generations of a family acquire most or all of the ownership interests of senior generations.</div>
    <div class="use use-r2"><h3>Balance Sheet Recapitalization</h3>Changes the debt and equity mixture of a company's balance sheet to a more optimal structure.</div>
    <div class="use use-r2"><h3>Refinancing</h3>Replacing one form or type of debt with another with better terms, conditions and flexibility.</div>
    <div class="use use-r3"><h3>Family Office Support</h3>Allows a family office to offset an investment in a company by allowing a junior capital provider to invest alongside them.</div>
    <div class="use use-r3"><h3>Senior Lender Enhancement or Transition</h3>When a company has grown beyond the means or interest of its senior bank but needs additional capital.</div>
    <div class="use use-r3"><h3>De-Lever Balance Sheet</h3>When a company has taken on too much debt and replaces some of it with other capital to provide flexibility.</div>
    <div class="use use-r3"><h3>Owner Dividend (Liquidity)</h3>When one or more owners take a non life-changing cash distribution to diversify their net worth.</div>
  </div>
  <div class="brand footer-brand"><span class="brand-dot"></span>PINEBROOK</div>
  <p class="footer-url">www.<b>pinebrookcapital</b>.com</p>
  <span class="page-no">5.</span>
</section>

<!-- 8. Contact -->
<section class="slide col-right row-4">
  <svg class="slide-frame" viewBox="0 0 441 249" preserveAspectRatio="none">
    <polygon points="0,0 30,0 0,90" fill="#4b4e52"/>
    <polygon points="412,0 441,0 441,249 350,249" fill="url(#bl1)"/>
  </svg>
  <svg class="contact-banner" viewBox="0 0 126 19" preserveAspectRatio="none">
    <polygon points="4,0 8,0 4,19 0,19" fill="#4b4e52"/>
    <polygon points="12,0 118,0 114,19 8,19" fill="#1f6fb8"/>
    <polygon points="122,0 126,0 122,19 118,19" fill="#4b4e52"/>
  </svg>
  <p class="contact-banner-text">CONTACT</p>
  <div class="contact-rail"></div>
  <ul class="contact-list">
    <li><strong>Daniel R. Marlowe</strong>Principal<br>41 Harbor View Road, Suite 210<br>Milford, CT 06460<br>Direct: (555) 210-4471<br>dmarlowe@<b>pinebrookcapital</b>.com</li>
    <li><strong>Boston Office</strong>18 Kestrel Park Drive, Suite 300<br>Salem, MA 01970<br><span class="phone">(555) 210-4400</span></li>
    <li><strong>San Francisco Office</strong>220 Marlow Street, Suite 480<br>San Francisco, CA 94105<br><span class="phone">(555) 388-1900</span></li>
  </ul>
  <div class="contact-photo" role="img" aria-label="Portrait photo of the principal"></div>
  <div class="brand footer-brand"><span class="brand-dot"></span>PINEBROOK</div>
  <p class="footer-url">www.<b>pinebrookcapital</b>.com</p>
  <span class="page-no">7.</span>
</section>

</body>
</html>
```